Velora Entertainment

Logo for business card design

Target Market(s)

potential film investors and screenwriters

Industry/Entity Type

Business

Contact Information for Business Card

as shown, website here is a placeholder position

Requirements
Must have
• great visual appeal
Nice to have
• harmony of colors; must evoke spirit of
• U.S.-China cooperation

```html
<!DOCTYPE html>
<html lang="en">
<head>
<meta charset="utf-8">
<title>Velora Entertainment – Business Card</title>
<link rel="stylesheet" href="https://fonts.googleapis.com/css2?family=Open+Sans:wght@400;600;700&display=swap">
<style>
  :root {
    --backdrop: #a2a2a3;
    --panel-grey: #8b8b8c;
    --back-grey: #868688;
    --card-white: #e4e4e7;
    --ink: #1e1e1e;
    --accent-red: #d01f2a;
    --accent-yellow: #e2bd0a;
    --accent-blue: #1c1d7c;
    --logo-ink: #2d2d30;
    --logo-light: #f2f2f4;
  }
  html, body {
    margin: 0;
    padding: 0;
    width: 1105px;
    height: 1200px;
    overflow: hidden;
    background: var(--backdrop);
    font-family: "Open Sans", Arial, sans-serif;
  }
  .canvas { position: relative; width: 1105px; height: 1200px; }

  .card {
    position: absolute;
    left: 182px;
    width: 746px;
    height: 427px;
    overflow: hidden;
  }
  .card--front { top: 119px; background: var(--card-white); }
  .card--back { top: 637px; background: var(--back-grey); }

  .info-panel {
    position: absolute;
    left: 0; top: 0;
    width: 329px; height: 100%;
    background: var(--panel-grey);
    color: var(--ink);
  }
  .accent-rule {
    position: absolute;
    left: 329px; top: 0;
    width: 4px; height: 100%;
  }
  .info-line {
    position: absolute;
    left: 43px;
    margin: 0;
    font-size: 20px;
    line-height: 1;
    white-space: nowrap;
  }
  .person-name {
    color: var(--accent-red);
    font-size: 25px;
    font-weight: 600;
  }
  .label { color: var(--accent-red); font-weight: 600; }
  .dotted-divider {
    position: absolute;
    left: 43px;
    width: 200px;
    border-top: 2px dotted var(--ink);
  }

  .brand-lockup {
    position: absolute;
    display: flex;
    align-items: center;
    gap: 12px;
    transform: translate(-50%, -50%);
    white-space: nowrap;
  }
  .brand-square {
    width: 34px; height: 34px;
    background: var(--accent-red);
  }
  .brand-name {
    font-size: 30px;
    font-weight: 700;
    color: var(--logo-ink);
  }
  .card--front .brand-lockup { left: 534px; top: 213px; }
  .card--back .brand-lockup { left: 373px; top: 213px; }
  .card--back .brand-name { color: var(--logo-light); }
</style>
</head>
<body>
<main class="canvas">
  <section class="card card--front" aria-label="Business card front">
    <div class="info-panel">
      <p class="info-line person-name" style="top:44px">Daniel Reyes</p>
      <p class="info-line" style="top:81px">CEO/Founder</p>
      <p class="info-line" style="top:108px">hello@veloraent.com</p>
      <div class="dotted-divider" style="top:151px"></div>
      <p class="info-line" style="top:179px">2140 Cedar Hollow Road</p>
      <p class="info-line" style="top:206px">Fairbanks, Alaska 99712</p>
      <p class="info-line" style="top:235px">www.veloraent.com</p>
      <div class="dotted-divider" style="top:279px"></div>
      <p class="info-line" style="top:311px"><span class="label">P :</span> 907 555 0142</p>
      <p class="info-line" style="top:339px"><span class="label">F :</span> 907 555 0187</p>
      <p class="info-line" style="top:367px"><span class="label">M :</span> 907 555 0163</p>
    </div>
    <svg class="accent-rule" width="4" height="427" viewBox="0 0 4 427" aria-hidden="true">
      <rect x="0" y="0" width="4" height="141" fill="var(--accent-blue)"/>
      <rect x="0" y="141" width="4" height="144" fill="var(--accent-yellow)"/>
      <rect x="0" y="285" width="4" height="142" fill="var(--accent-red)"/>
    </svg>
    <div class="brand-lockup">
      <span class="brand-square"></span>
      <span class="brand-name">Velora Entertainment</span>
    </div>
  </section>

  <section class="card card--back" aria-label="Business card back">
    <div class="brand-lockup">
      <span class="brand-square"></span>
      <span class="brand-name">Velora Entertainment</span>
    </div>
  </section>
</main>
</body>
</html>
```